Request for Business Card Design

Hi. My name is Marlene, I am looking for a new business card design for my company, Quarrow Signal Instruments, LLC. I really like the design you did for Tarsel Venture and was hoping you could do something similar using our full logo and our mark. I am also open to any raised texture design using our mark. I have attached our full logo, which would need to be somewhere on the card, as well as the mark in both outline and full form, as well as our brand colors / guide. The card does not have to be white, as long as our logo and mark appear. I actually like darker colored business cards more, but am open to all options. If you are interested in working with me, please let me know. We would also take the business card design into letterhead design if you can do that.

```html
<!DOCTYPE html>
<html lang="en">
<head>
<meta charset="utf-8">
<title>Quarrow Signal Instruments – Business Card</title>
<link rel="stylesheet" href="https://fonts.googleapis.com/css2?family=Archivo:wght@400;600;800&display=swap">
<style>
  :root {
    --stage: #2d2d2d;
    --card: #000000;
    --accent: #0a9cc4;
    --ink: #ffffff;
  }
  * { margin: 0; padding: 0; box-sizing: border-box; }
  html, body { width: 1200px; height: 1015px; overflow: hidden; }
  body {
    background: var(--stage);
    font-family: "Archivo", Arial, sans-serif;
    color: var(--ink);
    position: relative;
  }
  .card {
    position: absolute;
    width: 540px;
    height: 310px;
    background: var(--card);
    overflow: hidden;
    box-shadow: 0 14px 30px rgba(0,0,0,.45);
  }
  .card::after {
    content: "";
    position: absolute;
    left: 0; right: 0; bottom: 0;
    height: 7px;
    background: var(--accent);
  }
  .card--front { left: 110px; top: 130px; }
  .card--back { left: 560px; top: 545px; }

  /* front */
  .brand {
    position: absolute;
    left: 0; right: 0; top: 112px;
    display: flex;
    align-items: center;
    justify-content: center;
    gap: 18px;
  }
  .brand__dot {
    width: 54px; height: 54px;
    border-radius: 50%;
    background: var(--accent);
  }
  .brand__text { display: flex; flex-direction: column; }
  .brand__name {
    font-weight: 800;
    font-size: 40px;
    letter-spacing: 6px;
    line-height: 1;
  }
  .brand__tag {
    font-weight: 800;
    font-size: 11.5px;
    letter-spacing: 1.2px;
    margin-top: 4px;
  }

  /* back */
  .mark-circle {
    position: absolute;
    right: -30px; top: 40px;
    width: 250px; height: 250px;
    border-radius: 50%;
    border: 38px solid var(--accent);
  }
  .contact {
    position: absolute;
    left: 44px; top: 78px;
  }
  .contact__name {
    color: var(--accent);
    font-weight: 800;
    font-size: 22px;
    letter-spacing: .5px;
  }
  .contact__role {
    font-size: 13px;
    letter-spacing: .5px;
    margin-top: 2px;
  }
  .rule {
    width: 150px;
    height: 1px;
    background: var(--accent);
    margin: 12px 0 12px 14px;
  }
  .contact__list { list-style: none; margin-left: 14px; }
  .contact__list li {
    display: flex; align-items: center; gap: 8px;
    font-size: 14px; line-height: 22px;
  }
  .contact__list svg { width: 14px; height: 14px; fill: var(--accent); flex: none; }
  .contact__address {
    margin-left: 28px;
    font-size: 14px;
    line-height: 20px;
  }
</style>
</head>
<body>
  <section class="card card--front" aria-label="Card front">
    <div class="brand">
      <span class="brand__dot"></span>
      <div class="brand__text">
        <span class="brand__name">QUARROW</span>
        <span class="brand__tag">SIGNAL INSTRUMENTS</span>
      </div>
    </div>
  </section>

  <section class="card card--back" aria-label="Card back">
    <div class="mark-circle"></div>
    <div class="contact">
      <p class="contact__name">ELIAS BRANDT</p>
      <p class="contact__role">MANAGING DIRECTOR</p>
      <div class="rule"></div>
      <ul class="contact__list">
        <li><svg viewBox="0 0 24 24"><path d="M6.6 10.8a15.1 15.1 0 0 0 6.6 6.6l2.2-2.2a1 1 0 0 1 1-.25 11.4 11.4 0 0 0 3.6.57 1 1 0 0 1 1 1V20a1 1 0 0 1-1 1A17 17 0 0 1 3 4a1 1 0 0 1 1-1h3.5a1 1 0 0 1 1 1c0 1.25.2 2.45.57 3.57a1 1 0 0 1-.25 1z"/></svg>044-555 017 240</li>
        <li><svg viewBox="0 0 24 24"><path d="M2 5h20v14H2zM4 7v.4l8 5 8-5V7l-8 5z"/></svg>info@quarrowsignal.com</li>
        <li><svg viewBox="0 0 24 24"><path d="M12 2a10 10 0 1 0 0 20 10 10 0 0 0 0-20zm6.9 6h-3a15 15 0 0 0-1.3-3.9A8 8 0 0 1 18.9 8zM12 4c.9 1.2 1.6 2.6 2 4h-4c.4-1.4 1.1-2.8 2-4zM4.3 14a8 8 0 0 1 0-4h3.4a16 16 0 0 0 0 4zm.8 2h3a15 15 0 0 0 1.3 3.9A8 8 0 0 1 5.1 16zm3-8h-3a8 8 0 0 1 4.3-3.9A15 15 0 0 0 8.1 8zM12 20c-.9-1.2-1.6-2.6-2-4h4c-.4 1.4-1.1 2.8-2 4zm2.3-6H9.7a14 14 0 0 1 0-4h4.6a14 14 0 0 1 0 4zm.3 5.9a15 15 0 0 0 1.3-3.9h3a8 8 0 0 1-4.3 3.9zm1.7-5.9a16 16 0 0 0 0-4h3.4a8 8 0 0 1 0 4z"/></svg>www.quarrowsignal.com</li>
      </ul>
      <div class="rule"></div>
      <p class="contact__address">87 Ferrow Lane, Suite 4<br>80301, Boulder, USA</p>
    </div>
  </section>
</body>
</html>
```